Fresh-looking quality Label Design needed for Matcha Supplement

We need a Label Design for our new product Tide Vessel, a Matcha supplement, which uses just the best quality organic matcha from Japan.
We stand for the highest quality of our natural products.
Customers are from the DACH region and our products are slightly more expensive than from competitors.
The design should communicate a healthy lifestyle, high quality and the natural origin of the product, while also having a fresh and young touch. Designs for Inspiration are added in the files. Please take a look at them.
We think green colors work great, but the designer is free to choose colors he sees as a good fit. Kestro Vanta Omni Logo can also be used in black&white if that leads to a better-looking result.
The product text is fully in German and provided in the text file in the uploaded documents. There is only the need to copy and paste.
The center part of the product should be more visual (similar to the example uploads). We do not have a logo for the product name Tide Vessel, but it should just be "Tide Vessel" in a fitting font and in a green color. Font and logo should fit the overall design.
The side parts should include the rest of the text. The arrangement can be chosen as the designer sees fit, but the main layout should be appropriate for a product label.
All the text in the text document must be used. Text in Brackets "()" is just for better structure and should not be included on the finished design.
The product is of organic quality and completely vegan. The necessary bio seals and the vegan logo are in the uploaded documents and should all be used.
Product label dimensions: 140x55mm
Design should not look like a medical product, nor like an overly flashy gym supplement.

```html
<!DOCTYPE html>
<html lang="de">
<head>
<meta charset="utf-8">
<title>Tide Vessel – Etikett</title>
<link href="https://fonts.googleapis.com/css2?family=Roboto+Condensed:wght@400;700&family=Roboto:wght@400;700&display=swap" rel="stylesheet">
<style>
  :root {
    --green: #5aa13a;
    --green-soft: #cfe6c2;
    --green-pale: #e6f2de;
    --ink: #1a1a1a;
    --page: #e9e9e9;
    --label: #ffffff;
  }
  * { box-sizing: border-box; margin: 0; padding: 0; }
  html, body { width: 1200px; height: 1165px; overflow: hidden; background: var(--page); }
  body { position: relative; font-family: "Roboto", Arial, sans-serif; color: var(--ink); }

  .label {
    position: absolute; left: 40px; top: 362px; width: 1120px; height: 440px;
    background: var(--label); overflow: hidden;
  }
  .label__stripe { position: absolute; left: 0; right: 0; bottom: 2px; height: 8px; background: var(--green); }

  /* left panel */
  .usage__title { position: absolute; left: 44px; top: 26px; font-weight: 700; font-size: 19px; line-height: 24px; }
  .usage__dose {
    position: absolute; left: 26px; top: 60px; width: 268px; height: 48px;
    background: var(--green); color: #fff; font-weight: 700;
    font-size: 15.5px; line-height: 20px; text-align: center; padding-top: 4px;
  }
  .usage__warning {
    position: absolute; left: 31px; top: 122px; font-size: 13.2px; line-height: 17px; white-space: nowrap;
  }
  .seals { position: absolute; left: 32px; top: 356px; display: flex; gap: 12px; align-items: center; }
  .seal--hex { width: 52px; height: 44px; clip-path: polygon(25% 0,75% 0,100% 50%,75% 100%,25% 100%,0 50%); background: #dcdcdc; }
  .seal--eu { width: 62px; height: 44px; background: var(--green); }
  .seal--round { width: 58px; height: 58px; border-radius: 50%; background: var(--green-soft); }

  /* centre panel */
  .artwork {
    position: absolute; left: 320px; top: 0; width: 480px; height: 430px;
    background: radial-gradient(ellipse 50% 50% at 50% 50%,
      #ffffff 0%, #ffffff 34%, var(--green-pale) 55%, var(--green-pale) 78%, #ffffff 100%);
  }
  .brand {
    position: absolute; left: 320px; top: 168px; width: 480px; text-align: center;
    font-family: "Roboto Condensed", "Arial Narrow", sans-serif; font-weight: 700;
    font-size: 74px; line-height: 80px; color: var(--green); letter-spacing: -1px;
  }
  .brand sup { font-size: 26px; font-weight: 400; vertical-align: top; line-height: 38px; }
  .tagline {
    position: absolute; left: 410px; top: 246px; width: 300px; height: 37px;
    background: linear-gradient(90deg, rgba(207,230,194,0) 0%, var(--green-soft) 22%, var(--green-soft) 78%, rgba(207,230,194,0) 100%);
    font-family: "Roboto Condensed", "Arial Narrow", sans-serif; font-size: 23px; line-height: 37px; text-align: center;
  }
  .maker { position: absolute; left: 470px; top: 312px; width: 180px; text-align: center; }
  .maker__dot { display: block; width: 56px; height: 56px; border: 2px solid var(--ink); border-radius: 50%; margin: 0 auto 16px; }
  .maker__name { font-family: "Roboto", sans-serif; font-size: 16px; font-weight: 700; }
  .count {
    position: absolute; left: 408px; top: 371px; width: 58px; height: 61px; background: var(--green);
    border-radius: 8px 8px 0 0; color: #fff; text-align: center;
  }
  .count__num { font-size: 32px; line-height: 40px; }
  .count__unit { font-family: "Roboto Condensed", sans-serif; font-size: 11px; font-weight: 700; }
  .net { position: absolute; left: 700px; top: 392px; font-size: 24px; line-height: 28px; font-weight: 700; }

  /* right panel */
  .facts { position: absolute; left: 813px; top: 26px; width: 284px; }
  .facts__title { font-weight: 700; font-size: 17.5px; line-height: 24px; text-align: center; }
  .nutrition { margin-top: 6px; width: 280px; border: 2px solid var(--green); border-radius: 10px; overflow: hidden; }
  .nutrition__head {
    display: grid; grid-template-columns: 100px 102px 62px; background: var(--green); color: #fff;
    font-family: "Roboto Condensed", sans-serif; font-weight: 700; font-size: 14px; height: 28px; line-height: 28px; padding-left: 12px;
    white-space: nowrap;
  }
  .nutrition__body { padding: 6px 12px 8px; }
  .nutrition__row {
    display: grid; grid-template-columns: 124px 96px 36px; border-bottom: 1px solid var(--ink);
    font-family: "Roboto Condensed", sans-serif; font-size: 16px; line-height: 25px; white-space: nowrap;
  }
  .nutrition__row:last-child { border-bottom: none; }
  .notes { margin-top: 12px; font-size: 13px; line-height: 17px; }
  .ingredients { margin-top: 12px; font-size: 13px; line-height: 17px; }
  .contact { margin-top: 20px; font-size: 13px; line-height: 17px; }
</style>
</head>
<body>
<section class="label">
  <h2 class="usage__title">VERZEHREMPFEHLUNG</h2>
  <p class="usage__dose">2 Kapseln täglich mit ausreichend<br>Flüssigkeit einnehmen.</p>
  <p class="usage__warning"><b>WARNING:</b> Nahrungsergänzungsmittel sollten<br>nicht als Ersatz für eine abwechslungsreiche<br>und ausgewogene Ernährung und eine<br>gesunde Lebensweise verwendet werden.<br>Die angegebene empfohlene tägliche Verzehr-<br>menge darf nicht überschritten werden.<br>Das Produkt bitte außerhalb der Reichweite<br>von Kleinkindern aufbewahren.<br>Für Kinder und Schwangere nicht<br>empfohlen. Kühl, trocken und lichtge-<br>schützt aufbewahren. Mindestens<br>haltbar bis Ende: siehe Bodenaufdruck.</p>
  <div class="seals">
    <span class="seal--hex"></span>
    <span class="seal--eu"></span>
    <span class="seal--round"></span>
    <span class="seal--round"></span>
  </div>

  <div class="artwork" role="img" aria-label="Scattered hand-drawn green leaf illustrations around the product name"></div>
  <h1 class="brand">Tide Vessel<sup>®</sup></h1>
  <p class="tagline">mit japanischem Bio Matcha</p>
  <div class="maker"><span class="maker__dot"></span><span class="maker__name">Kestro Vanta Omni</span></div>
  <div class="count"><div class="count__num">60</div><div class="count__unit">KAPSELN</div></div>
  <div class="net">℮ 24g</div>

  <div class="facts">
    <h2 class="facts__title">NAHRUNGSERGÄNZUNGSMITTEL<br>MIT JAPANISCHEM BIO MATCHA</h2>
    <div class="nutrition">
      <div class="nutrition__head"><span>Nährwerte</span><span>je Tagesdosis*</span><span>% NRV**</span></div>
      <div class="nutrition__body">
        <div class="nutrition__row"><span>Bio Matcha</span><span>600mg</span><span>***</span></div>
        <div class="nutrition__row"><span>davon Polyphenole</span><span>175mg</span><span>***</span></div>
        <div class="nutrition__row"><span>davon Katechine</span><span>103mg</span><span>***</span></div>
        <div class="nutrition__row"><span>davon EGCG</span><span>48mg</span><span>***</span></div>
      </div>
    </div>
    <p class="notes">*Entspricht 2 Kapseln.<br>**Prozentsatz der Nährstoffbezugswerte gem.<br>VO (EU) Nr. 1169/2011.<br>***Keine Nährstoffbezugswerte bekannt.</p>
    <p class="ingredients"><b>Zutaten:</b> Matcha aus kontrolliert biologischem<br>Anbau (kbA, BIO) in Kyushu (Japan), vegane<br><b>Kapsel:</b> Hydroxypropylmethylcellulose (HPMC).</p>
    <p class="contact"><b>Kontakt:</b> Kestro Vanta Omni,<br>Lindenweg 12, 8020 Graz</p>
  </div>

  <div class="label__stripe"></div>
</section>
</body>
</html>
```